Figure for presentation on a hybrid research project

We need a figure that shows a series of 6 technical projects feeding into 3 multidisciplinary hybrid projects.
The concept is a ring of 6 technical projects, which could look like a 6 colour swirl (see
https://en.plorvanex.org/wiki/Vector_graphics for an example of a 4 colour swirl.)
The 3 hybrid projects sit in the centre because they rely on input from many of the surrounding technical projects.
I've drawn a rough version in Powerpoint - see attached file uploaded. Note, in my example I couldn't draw the swirling outer ring and the colour selection is poor. The acronym for the overall Centre using the figure is VexORDA, so we will have a mint leaf and turquoise green in the logo, plus also nerves, since we will be researching neural interconnections.
We ABSOLUTELY NEED the final form of the figure to include vector graphics formats (including a form that can be edited in Photoshop) because we may need to change the title of the technical projects or of the hybrid projects at short notice ourselves.

Target Market(s)

Academic: eminent scientists and engineers

Industry/Entity Type

Technical

Font styles to use
Sans Serif

Colors
04a990

Requirements
Must have
• The projects around the ring with all project titles legible; the final figure will be reduced to no more than 8cm x 8cm in the proposal (probably less).
• Only one colour selected, because we have included that colour in the logo that we are having designed. Otherwise, a colour series around the ring that is pleasant, and another compatible colour series for the inter 3 projects.
• We ABSOLUTELY NEED the final form of the figure to include vector graphics formats (including a form that can be edited in Photoshop) because we may need to change the title of the technical projects or of the hybrid projects at short notice ourselves.
Nice to have
• See the figure we uploaded; that's the essence
• HOWEVER VIP: two of the titles around the outer ring have changed slightly.
• Computational Modelling is now Neuronal Modelling and
• Signal Processing is now Non-Invasive Interfaces (note that I've now changed the titles on the uploaded figure)

```html
<!DOCTYPE html>
<html lang="en">
<head>
<meta charset="utf-8">
<title>Hybrid Research Projects Figure</title>
<link href="https://fonts.googleapis.com/css2?family=Arimo:wght@400&display=swap" rel="stylesheet">
<style>
  :root {
    --canvas-bg: #434244;
    --ring-green: #04a990;
    --core-green: #0e7561;
    --line-white: #ffffff;
    --label-dark: #3b3b3d;
    --core-text: #ffffff;
  }
  html, body {
    margin: 0;
    padding: 0;
    overflow: hidden;
    background: var(--canvas-bg);
  }
  .figure-canvas {
    width: 1200px;
    height: 1000px;
    position: relative;
    overflow: hidden;
    background: var(--canvas-bg);
  }
  .figure-canvas svg {
    display: block;
  }
  .outer-disc { fill: var(--ring-green); stroke: var(--line-white); stroke-width: 2; }
  .swirl-edge { fill: none; stroke: var(--line-white); stroke-width: 2; }
  .project-label {
    font-family: "Arimo", Arial, sans-serif;
    font-size: 24px;
    fill: var(--label-dark);
  }
  .core-ring { fill: #f4f4f4; stroke: #c9c9c9; stroke-width: 1.5; }
  .core-disc { fill: var(--core-green); }
  .core-divider { stroke: var(--line-white); stroke-width: 2; }
  .hybrid-label {
    font-family: "Arimo", Arial, sans-serif;
    font-size: 28px;
    fill: var(--core-text);
  }
</style>
</head>
<body>
<div class="figure-canvas">
  <svg width="1200" height="1000" viewBox="0 0 1200 1000" role="img" aria-label="Six technical projects in a swirling ring feeding three hybrid projects at the centre">
    <defs>
      <radialGradient id="core-glow" cx="50%" cy="50%" r="50%">
        <stop offset="70%" stop-color="#0a3a30" stop-opacity="0.9"/>
        <stop offset="100%" stop-color="#04a990" stop-opacity="0"/>
      </radialGradient>
      <clipPath id="outer-clip">
        <circle cx="584" cy="452" r="348"/>
      </clipPath>
    </defs>

    <!-- technical project ring -->
    <g class="technical-ring">
      <circle class="outer-disc" cx="584" cy="452" r="348"/>
      <g clip-path="url(#outer-clip)">
        <path class="swirl-edge" d="M545,312 A105,105 0 0 1 585,105"/>
        <path class="swirl-edge" d="M693,360 A103,103 0 0 1 880,270"/>
        <path class="swirl-edge" d="M712,510 A103,103 0 0 1 890,620"/>
        <path class="swirl-edge" d="M590,593 A104,104 0 0 1 585,801"/>
        <path class="swirl-edge" d="M472,545 A105,105 0 0 1 288,640"/>
        <path class="swirl-edge" d="M452,400 A105,105 0 0 1 287,285"/>
      </g>

      <text class="project-label" x="522" y="198">Living electrode</text>
      <text class="project-label" x="703" y="346">Gene regulated</text>
      <text class="project-label" x="748" y="380">interfaces</text>
      <text class="project-label" x="676" y="605">Electro-modulated</text>
      <text class="project-label" x="682" y="638">interfaces</text>
      <text class="project-label" x="479" y="663">Optrode</text>
      <text class="project-label" x="479" y="697">interfaces</text>
      <text class="project-label" x="280" y="499">Neuronal</text>
      <text class="project-label" x="280" y="533">modelling</text>
      <text class="project-label" x="315" y="296">Non-invasive</text>
      <text class="project-label" x="315" y="330">Interfaces</text>
    </g>

    <!-- hybrid project core -->
    <g class="hybrid-core">
      <circle cx="584" cy="452" r="170" fill="url(#core-glow)"/>
      <circle class="core-ring" cx="584" cy="452" r="138"/>
      <circle class="core-disc" cx="584" cy="452" r="128"/>
      <line class="core-divider" x1="584" y1="452" x2="522" y2="340"/>
      <line class="core-divider" x1="584" y1="452" x2="712" y2="452"/>
      <line class="core-divider" x1="584" y1="452" x2="520" y2="563"/>

      <text class="hybrid-label" transform="translate(622,392) rotate(36)" text-anchor="middle" dominant-baseline="middle">Perception</text>
      <text class="hybrid-label" transform="translate(620,513) rotate(-32)" text-anchor="middle" dominant-baseline="middle">Action</text>
      <text class="hybrid-label" transform="translate(512,452) rotate(-90)" text-anchor="middle" dominant-baseline="middle">Brain wiring</text>
    </g>
  </svg>
</div>
</body>
</html>
```